Need a redesign for our Wordpress Credit report website

Hi, We need someone to redesign our Wordpress credit report website, lumenledger.co.za. The designer will be responsible for the following pages:
- home page
- blog page
- single post
- dashboard
- credit report page

About LumenLedger.co.za
Lumen Ledger is a consumer focussed credit report platform where South African citizens can get an easy to understand credit report that shows them where to improve their credit scores.

```html
<!DOCTYPE html>
<html lang="en">
<head>
<meta charset="utf-8">
<title>Lumen Ledger – Check Your Credit Score</title>
<link href="https://fonts.googleapis.com/css2?family=Arimo:ital,wght@0,400;0,700;1,400&display=swap" rel="stylesheet">
<style>
:root{
  --blue:#2b6fc7;
  --blue-dark:#1f60b6;
  --green:#8dc63f;
  --ink:#222;
  --grey:#666;
  --light:#f2f2f2;
  --white:#fff;
  --star:#f7941d;
}
*{box-sizing:border-box;margin:0;padding:0}
html,body{width:1200px;height:3101px;overflow:hidden}
body{font-family:"Arimo",Arial,sans-serif;color:var(--ink);background:var(--white);position:relative}
.abs{position:absolute}
.center-x{left:0;width:1200px;text-align:center}

/* header */
.site-header{position:absolute;top:0;left:0;width:1200px;height:86px;background:var(--white)}
.brand{position:absolute;left:112px;top:24px;display:flex;align-items:center;gap:10px}
.brand-dot{width:34px;height:34px;border-radius:50%;background:var(--green)}
.brand-name{font-size:24px;color:var(--blue)}
.main-nav{position:absolute;top:38px;font-size:15px}
.main-nav a{position:absolute;white-space:nowrap;color:#333;text-decoration:none}
.main-nav a.active{color:var(--blue)}

/* hero */
.hero{position:absolute;top:86px;left:0;width:1200px;height:623px;background:var(--blue);color:var(--white)}
.hero h1{position:absolute;left:112px;top:48px;font-size:23px;line-height:44px;font-weight:700}
.hero .cta{position:absolute;left:111px;top:141px;font-size:23px;font-weight:700;color:var(--green)}
.field{position:absolute;border:1px solid rgba(255,255,255,.85);font-size:14px;padding:15px 7px;height:52px}
.agree{position:absolute;left:112px;top:387px;font-size:14px;display:flex;align-items:center;gap:6px}
.agree span.box{width:10px;height:10px;border:1px solid var(--white);border-radius:2px}
.btn-score{position:absolute;left:112px;top:422px;width:350px;height:52px;background:var(--green);color:#1a2a10;font-size:16px;font-weight:700;display:flex;align-items:center;justify-content:center;box-shadow:0 2px 3px rgba(0,0,0,.2)}
.disclaimer{position:absolute;left:111px;top:493px;width:360px;font-size:13px;line-height:25.5px}
.device-art{position:absolute;left:598px;top:76px;width:473px;height:365px;border-radius:10px;background:linear-gradient(135deg,#e9eef5,#c9d4e2 60%,#9aa8bb)}
.hero-list{position:absolute;left:598px;top:430px;list-style:none;font-size:14.5px}
.hero-list li{height:34.4px;display:flex;align-items:center;gap:8px}

.tick{width:13px;height:13px;flex:none}

/* section titles */
.sec-title{font-size:41px;font-weight:700;color:var(--blue);letter-spacing:.3px}
.rule{height:3px;width:87px;background:var(--green)}

/* features */
.features{position:absolute;top:709px;left:0;width:1200px;height:490px;border-bottom:1px solid #ddd}
.feature-list{position:absolute;left:111px;top:181px;list-style:none;font-size:14.5px}
.feature-list li{height:34.3px;display:flex;align-items:center;gap:9px}
.features-art{position:absolute;left:586px;top:73px;width:504px;height:358px;border-radius:46% 50% 40% 44%;background:radial-gradient(circle at 55% 50%,#f3f6ff,#d9e2fb 60%,#c4d1f6)}

/* testimonials */
.testimonials{position:absolute;top:1199px;left:0;width:1200px;height:478px}
.quote{font-size:15.5px;font-style:italic;color:var(--grey);line-height:34.5px;width:860px;margin:0 auto}
.arrow-btn{position:absolute;top:224px;width:40px;height:40px;border:1.5px solid #999;border-radius:50%}
.avatar{border-radius:50%;background:linear-gradient(135deg,#c9ced8,#8b95a5)}
.stars{color:var(--star);font-size:14px;letter-spacing:-1px}

/* reviews */
.reviews{position:absolute;top:1677px;left:0;width:1200px;height:574px;background:var(--light)}
.review-card{position:absolute;top:177px;width:308px;height:276px;background:var(--white);box-shadow:0 2px 6px rgba(0,0,0,.15);text-align:center}
.review-card .avatar{width:46px;height:46px;margin:28px auto 0}
.review-card p{font-size:13px;font-style:italic;color:var(--grey);line-height:25px;margin:12px 18px 0}
.review-card .name{color:var(--blue);font-size:13.5px;margin-top:8px}
.review-card .count{font-size:13px;font-style:italic;color:#444;margin-top:6px}
.review-card .stars{margin-top:6px;font-size:13px}
.dots{position:absolute;top:2174px;left:533px;display:flex;gap:5.5px}
.dots span{width:12px;height:12px;border:1.5px solid #888;border-radius:50%}
.dots span.on{border-color:var(--blue)}

/* why */
.why{position:absolute;top:2251px;left:0;width:1200px;height:544px}
.why-art{position:absolute;left:117px;top:90px;width:427px;height:247px;border-radius:50% 50% 12px 12px;background:linear-gradient(160deg,#e6e8ee,#c8ccd8 55%,#2c6a7a)}
.why h2{position:absolute;left:599px;top:96px;font-size:29px;font-weight:700;color:var(--blue)}
.why h3{position:absolute;font-size:16px;font-weight:700}
.why p{position:absolute;font-size:14px;color:var(--grey);line-height:27.4px}

/* payments */
.payments{position:absolute;top:2795px;left:0;width:1200px;height:78px;display:flex;justify-content:center;align-items:center;gap:26px}
.pay{font-size:13px;font-weight:700;color:#555;display:flex;align-items:center;gap:5px}
.pay i{width:10px;height:10px;background:#bbb;border-radius:50%}

/* footer */
.site-footer{position:absolute;top:2873px;left:0;width:1200px;height:228px;background:var(--blue-dark);color:var(--white)}
.foot-col{position:absolute;top:49px}
.foot-col h4{font-size:16px;font-weight:700;margin-bottom:12px;margin-left:1px}
.foot-col a{display:block;color:var(--white);text-decoration:none;font-size:14.5px;line-height:27.3px}
.social{position:absolute;top:76px;left:834px;display:flex;gap:15px}
.social span{width:38px;height:38px;border:1.5px solid var(--white);border-radius:50%}
.copyright{position:absolute;right:112px;top:129px;font-size:14px}
</style>
</head>
<body>

<header class="site-header">
  <div class="brand"><span class="brand-dot"></span><span class="brand-name">Lumen Ledger</span></div>
  <nav class="main-nav">
    <a class="active" style="left:672px">HOME</a>
    <a style="left:746px">ARTICLES</a>
    <a style="left:847px">ABOUT</a>
    <a style="left:928px">CONTACT</a>
    <a style="left:1027px"><svg width="10" height="12" viewBox="0 0 10 12" style="vertical-align:-1px"><circle cx="5" cy="3" r="3" fill="#2b6fc7"/><path d="M0 12c0-4 2-6 5-6s5 2 5 6z" fill="#2b6fc7"/></svg> LOGIN</a>
  </nav>
</header>

<section class="hero">
  <h1>CHECK YOUR CREDIT SCORE<br>WITHIN SECONDS</h1>
  <div class="cta">GET STARTED NOW</div>
  <div class="field" style="left:112px;top:194px;width:171px">ID number</div>
  <div class="field" style="left:290px;top:194px;width:172px">First Name</div>
  <div class="field" style="left:112px;top:258px;width:171px">Last Name</div>
  <div class="field" style="left:290px;top:258px;width:172px">Primary Email</div>
  <div class="field" style="left:112px;top:318px;width:350px">Phone Number</div>
  <div class="agree"><span class="box"></span>I agree with the terms and conditions</div>
  <div class="btn-score">SHOW MY SCORE</div>
  <p class="disclaimer">By signing up and agreeing with the terms you authorise LumenLedger.co.za to request your credit report from the bureaus and display it within the site.</p>
  <div class="device-art" role="img" aria-label="Laptop and tablet showing an example credit report with a 740 score gauge"></div>
  <ul class="hero-list">
    <li><svg class="tick" viewBox="0 0 13 13"><circle cx="6.5" cy="6.5" r="6.5" fill="#8dc63f"/><path d="M5 3.8l2.8 2.7L5 9.2" stroke="#2b6fc7" stroke-width="1.6" fill="none"/></svg>See your most recent credit score</li>
    <li><svg class="tick" viewBox="0 0 13 13"><circle cx="6.5" cy="6.5" r="6.5" fill="#8dc63f"/><path d="M5 3.8l2.8 2.7L5 9.2" stroke="#2b6fc7" stroke-width="1.6" fill="none"/></svg>Get access to your full credit profile</li>
    <li><svg class="tick" viewBox="0 0 13 13"><circle cx="6.5" cy="6.5" r="6.5" fill="#8dc63f"/><path d="M5 3.8l2.8 2.7L5 9.2" stroke="#2b6fc7" stroke-width="1.6" fill="none"/></svg>See who has been looking at your profile</li>
    <li><svg class="tick" viewBox="0 0 13 13"><circle cx="6.5" cy="6.5" r="6.5" fill="#8dc63f"/><path d="M5 3.8l2.8 2.7L5 9.2" stroke="#2b6fc7" stroke-width="1.6" fill="none"/></svg>See if you have any adverse or Blacklistings</li>
  </ul>
</section>

<section class="features">
  <h2 class="sec-title abs" style="left:110px;top:84px">SYSTEM FEATURES</h2>
  <div class="rule abs" style="left:112px;top:149px"></div>
  <ul class="feature-list">
    <li><svg class="tick" viewBox="0 0 13 13"><circle cx="6.5" cy="6.5" r="6.5" fill="#8dc63f"/><path d="M5 3.8l2.8 2.7L5 9.2" stroke="#fff" stroke-width="1.6" fill="none"/></svg>Dispute generator - easily manage disputes</li>
    <li><svg class="tick" viewBox="0 0 13 13"><circle cx="6.5" cy="6.5" r="6.5" fill="#8dc63f"/><path d="M5 3.8l2.8 2.7L5 9.2" stroke="#fff" stroke-width="1.6" fill="none"/></svg>Budget tool - easily create a budget</li>
    <li><svg class="tick" viewBox="0 0 13 13"><circle cx="6.5" cy="6.5" r="6.5" fill="#8dc63f"/><path d="M5 3.8l2.8 2.7L5 9.2" stroke="#fff" stroke-width="1.6" fill="none"/></svg>Improve your credit score eBook</li>
    <li><svg class="tick" viewBox="0 0 13 13"><circle cx="6.5" cy="6.5" r="6.5" fill="#8dc63f"/><path d="M5 3.8l2.8 2.7L5 9.2" stroke="#fff" stroke-width="1.6" fill="none"/></svg>Personal Budgeting Spreadsheet</li>
    <li><svg class="tick" viewBox="0 0 13 13"><circle cx="6.5" cy="6.5" r="6.5" fill="#8dc63f"/><path d="M5 3.8l2.8 2.7L5 9.2" stroke="#fff" stroke-width="1.6" fill="none"/></svg>Perfect score video course</li>
    <li><svg class="tick" viewBox="0 0 13 13"><circle cx="6.5" cy="6.5" r="6.5" fill="#8dc63f"/><path d="M5 3.8l2.8 2.7L5 9.2" stroke="#fff" stroke-width="1.6" fill="none"/></svg>Personal Finance Video Tutorials</li>
    <li><svg class="tick" viewBox="0 0 13 13"><circle cx="6.5" cy="6.5" r="6.5" fill="#8dc63f"/><path d="M5 3.8l2.8 2.7L5 9.2" stroke="#fff" stroke-width="1.6" fill="none"/></svg>Dedicated 24/7 Support</li>
  </ul>
  <div class="features-art" role="img" aria-label="Illustration of a credit report clipboard, bank card, coins and a person with a magnifying glass"></div>
</section>

<section class="testimonials">
  <h2 class="sec-title abs center-x" style="top:47px">USER TESTIMONIALS</h2>
  <div class="rule abs" style="left:557px;top:112px"></div>
  <svg class="abs" style="left:572px;top:154px" width="56" height="48" viewBox="0 0 56 48"><path d="M2 48V26C2 10 10 2 24 0v9c-7 2-11 7-11 15h11v24zM32 48V26C32 10 40 2 54 0v9c-7 2-11 7-11 15h11v24z" fill="#111"/></svg>
  <span class="arrow-btn" style="left:43px"><svg width="37" height="37" viewBox="0 0 37 37"><path d="M21 12l-6 6.5 6 6.5" stroke="#888" stroke-width="1.5" fill="none"/></svg></span>
  <span class="arrow-btn" style="left:1109px"><svg width="37" height="37" viewBox="0 0 37 37"><path d="M16 12l6 6.5-6 6.5" stroke="#888" stroke-width="1.5" fill="none"/></svg></span>
  <p class="quote abs" style="left:170px;top:220px;text-align:center">The report was accurate and gave me a good understanding of my current credit status. I found it interesting the way the scoring worked and really enjoyed reading it...guess because I am doing well with managing credit.</p>
  <div class="avatar abs" style="left:548px;top:298px;width:104px;height:104px" role="img" aria-label="Customer family photo"></div>
  <div class="stars abs center-x" style="top:416px">★★★★★</div>
</section>

<section class="reviews">
  <h2 class="sec-title abs center-x" style="top:67px">CLIENT REVIEWS</h2>
  <div class="rule abs" style="left:557px;top:132px"></div>
  <article class="review-card" style="left:111px">
    <div class="avatar" role="img" aria-label="Reviewer photo"></div>
    <p>The credit report is easy to use, informative and accurate to the date. Helps me to manage my financial well-being.</p>
    <div class="name">Marlene Vosloo</div><div class="count">28 reviews</div><div class="stars">★★★★★</div>
  </article>
  <article class="review-card" style="left:445px">
    <div class="avatar" role="img" aria-label="Reviewer photo"></div>
    <p>Their customer support team has been very impressive. The tools and knowledge they shared were of great practical use.</p>
    <div class="name">Carina Steyn</div><div class="count">2 reviews</div><div class="stars">★★★★★</div>
  </article>
  <article class="review-card" style="left:780px">
    <div class="avatar" role="img" aria-label="Reviewer photo"></div>
    <p>Excellent credit report service. They respond to queries promptly, and have a very detailed credit report which is helpful and informative</p>
    <div class="name">Peak Form SA</div><div class="count">2 reviews</div><div class="stars">★★★★★</div>
  </article>
</section>
<div class="dots"><span class="on"></span><span></span><span></span><span></span><span></span><span></span><span></span><span></span></div>

<section class="why">
  <div class="why-art" role="img" aria-label="Illustration of two people working on laptops beside a large bank card and leaves"></div>
  <h2>WHY GET YOUR SCORE FROM US?</h2>
  <div class="rule abs" style="left:601px;top:148px"></div>
  <h3 style="left:601px;top:178px">We don't abuse your personal information:</h3>
  <p style="left:600px;top:210px;width:490px">Companies that give out free credit scores use your personal information to sell you financial products. That's how they can afford to give it to you for free. We believe that your personal information should be protected and not abused. That's why we ask a small fee. It enables us to protect your information and not abuse it.</p>
  <h3 style="left:601px;top:366px">Our report is super easy to understand:</h3>
  <p style="left:600px;top:396px;width:500px">Our credit report is one of the easiest reports to understand. The report is clearly laid out and you will see immediately if you can apply for finance, if you are blacklisted, and where you can improve.</p>
  <h3 style="left:113px;top:366px">300,000 + South Africans have trusted us:</h3>
  <p style="left:113px;top:396px;width:480px">Since 2008 we have helped over 300,000 South Africans make sense of their credit reports, so you can rest assured knowing that we have a proven track record and that you are in safe hands with us.</p>
</section>

<div class="payments">
  <span class="pay"><i></i>CardOne</span>
  <span class="pay"><i></i>Paylo</span>
  <span class="pay"><i></i>WalletGo</span>
  <span class="pay"><i></i>NovaPay</span>
</div>

<footer class="site-footer">
  <div class="foot-col" style="left:111px"><h4>TERMS</h4><a>General Terms Of Use</a><a>Exclusion Of Liability</a><a>Security Policy</a><a>Privacy Policy</a></div>
  <div class="foot-col" style="left:290px"><h4>PURCHASE</h4><a>Delivery Policy</a><a>Data Policy</a><a>Refund Policy</a><a>Charges And Fees</a></div>
  <div class="foot-col" style="left:472px"><h4>QUICK LINKS</h4><a>About Us</a><a>Articles</a><a>Contact Us</a><a>Login</a></div>
  <div class="social">
    <span role="img" aria-label="Circlely"></span><span role="img" aria-label="Snapframe"></span><span role="img" aria-label="Chirpline"></span><span role="img" aria-label="ViewTube"></span><span role="img" aria-label="PlusNet"></span>
  </div>
  <div class="copyright">© 2022 All Rights Reserved</div>
</footer>

</body>
</html>
```